Larkmoor Drones Business Card

We are a new company based in Central Queensland, Australia that uses specalised drones (Voskel Ferra Q80) to undertake mainly agricultural operations, like spraying weeds, spraying crops, spreading seed etc. I have attached a Plimbo proof of a card I was thinking along the lines of - purely a start point. The drone used in the business card MUST be a Voskel Ferra Q80.
I am very open to other ideas, especially fonts and layout. I don't have website etc set up yet.
The images are stock and easily interchangeable, I just ask that any background images reflect the local central Queensland area. The photo of the drone is not even complete (propellers cut off) and I need a new stock photo – I’m not sure if this is an issue, or I can pay for an image if need be. PLEASE FIND AN FERRA Q80 image - 4 sprayers, not 6.
The logo/business name is very draft and looking for further ideas, ideally incorporating drones or agriculture design elements into the design of the business name. The business name needs work on the graphic/design – it is a draft that I have included, the drone propellers (being a different colour) are DRAFT only and intended for changes. PLEASE DO NOT USE THE DRONE PORPELLER I HAVE USED AS A DRAFT. TRY TO FIND SOMETHING ELSE.. The arrow is a shape and not aligned in any way, I would also like ideas on different fonts and additional elements, like air streams, aviation elements, aviation or country western (farming like) themes and fonts etc.
Ideally looking at staying within the blue, green and yellow colours, keeping with an natural, outdoorsy, environmental feel.

Target Market(s)

Farmers, Agriculture, Local Governments, Land Managers

Industry/Entity Type

Agriculture, Drones, Aviation

Contact Information for Business Card

Agricultural Drone (Voskel Ferra Q80), Farming, Business Name.

Font styles to use
Sans Serif

Colors
0054AA
0677BA
7BADD7
CADEEF
E8F1F8
0094D4
00A9DD
6FCCEA
C7EBF8
E9F6FB
00AB8E
00BBA5
67D7C9
C6EFE9
E9F9F6
59FF00
82FF00
B8FF75
E3FFCB
F4FFEA

Requirements
Must have
• Voskel Ferra Q80 Drone
Should not have
• Tractors

```html
<!DOCTYPE html>
<html lang="en">
<head>
<meta charset="utf-8">
<title>Larkmoor Drones Business Card</title>
<link rel="stylesheet" href="https://fonts.googleapis.com/css2?family=Alfa+Slab+One&family=Cinzel:wght@500&family=Poppins:wght@400;500;800&display=swap">
<style>
  :root {
    --stage: #222222;
    --navy: #4a5a73;
    --olive: #7f8f3a;
    --white: #ffffff;
    --ink: #2b2f36;
    --sky-top: #e9a53a;
    --sky-mid: #d9c79a;
    --field: #7fa03a;
    --field-deep: #4f7326;
  }
  * { box-sizing: border-box; margin: 0; padding: 0; }
  html, body {
    width: 1200px; height: 800px; overflow: hidden;
    background: var(--stage);
    font-family: "Poppins", sans-serif;
  }
  .stage {
    width: 1200px; height: 800px;
    display: flex; align-items: center; justify-content: center; gap: 40px;
  }
  .card {
    position: relative;
    width: 540px; height: 315px;
    border-radius: 22px;
    overflow: hidden;
    background: var(--white);
  }

  /* Front */
  .card-front .field-photo {
    position: absolute; inset: 0 0 145px 0;
    background: linear-gradient(180deg, var(--sky-top) 0%, var(--sky-mid) 45%, var(--field) 72%, var(--field-deep) 100%);
  }
  .services {
    position: absolute; top: 26px; left: 0; right: 0;
    text-align: center;
    font-family: "Alfa Slab One", serif;
    font-size: 20px; letter-spacing: 5px;
    color: var(--navy);
  }
  .front-band {
    position: absolute; left: 0; right: 0; top: 170px; height: 92px;
    background: var(--navy);
    display: flex; flex-direction: column; align-items: center; justify-content: center;
  }
  .brand-name {
    font-family: "Poppins", sans-serif; font-weight: 800;
    color: var(--white);
    font-size: 34px; line-height: 1; text-transform: uppercase; text-align: center;
  }
  .front-foot {
    position: absolute; left: 0; right: 0; bottom: 0; height: 53px;
    background: var(--olive);
    display: flex; align-items: flex-start; justify-content: center; padding-top: 8px;
  }
  .tagline {
    font-family: "Cinzel", serif; font-weight: 500;
    font-size: 12px; letter-spacing: 1px;
    color: var(--ink);
  }

  /* Back */
  .card-back .waves { position: absolute; inset: 0; }
  .back-brand {
    position: absolute; top: 34px; right: 34px; text-align: right;
  }
  .back-brand .brand-name { color: var(--navy); font-size: 28px; }
  .back-brand .tagline { display: block; margin-top: 4px; font-size: 10px; }
  .person {
    position: absolute; top: 96px; left: 30px;
  }
  .person-name {
    font-weight: 800; font-size: 30px; line-height: 1.05; color: var(--navy);
  }
  .person-role {
    font-weight: 500; font-size: 13px; color: var(--navy); letter-spacing: 0.5px;
  }
  .contact-list {
    position: absolute; left: 42px; top: 214px;
    list-style: none;
  }
  .contact-list li {
    display: flex; align-items: center; gap: 8px;
    color: var(--white); font-size: 11px; line-height: 17px; height: 17px;
  }
  .contact-icon { width: 13px; height: 13px; flex: none; }
</style>
</head>
<body>
<main class="stage">

  <section class="card card-front" aria-label="Card front">
    <div class="field-photo" role="img" aria-label="Photo of a Voskel Ferra Q80 spraying drone hovering over a green Central Queensland crop field at sunset"></div>
    <p class="services">SPRAY · WEED · SEED · FEED</p>
    <div class="front-band">
      <p class="brand-name">Larkmoor<br>Drones</p>
    </div>
    <div class="front-foot">
      <span class="tagline">SERVICING CENTRAL QUEENSLAND</span>
    </div>
  </section>

  <section class="card card-back" aria-label="Card back">
    <svg class="waves" viewBox="0 0 540 315" preserveAspectRatio="none" aria-hidden="true">
      <path d="M0,176 C170,150 340,146 540,98 L540,106 C330,154 170,156 0,180Z" fill="var(--olive)"/>
      <path d="M0,184 C160,156 330,152 540,114 L540,132 C320,166 150,174 0,198Z" fill="var(--navy)"/>
      <path d="M0,204 C160,180 320,178 540,140 L540,315 L0,315Z" fill="var(--olive)"/>
    </svg>

    <div class="back-brand">
      <p class="brand-name">Larkmoor Drones</p>
      <span class="tagline">SERVICING CENTRAL QUEENSLAND</span>
    </div>

    <div class="person">
      <p class="person-name">Mara Telvin</p>
      <p class="person-role">Founder &amp; CEO</p>
    </div>

    <ul class="contact-list">
      <li>
        <svg class="contact-icon" viewBox="0 0 14 14" aria-hidden="true"><circle cx="7" cy="7" r="7" fill="#fff"/><path d="M4.6,3.6 l1.2,0 .5,1.6 -.8,.7 c.4,.9 1.1,1.6 2,2 l.7,-.8 1.6,.5 0,1.2 c-3,.3 -5.5,-2.2 -5.2,-5.2z" fill="var(--olive)"/></svg>
        (555) 014-3372
      </li>
      <li>
        <svg class="contact-icon" viewBox="0 0 14 14" aria-hidden="true"><circle cx="7" cy="7" r="7" fill="#fff"/><g fill="none" stroke="var(--olive)" stroke-width=".8"><circle cx="7" cy="7" r="3.8"/><ellipse cx="7" cy="7" rx="1.6" ry="3.8"/><path d="M3.2,7 h7.6"/></g></svg>
        www.larkmoorsite.com
      </li>
      <li>
        <svg class="contact-icon" viewBox="0 0 14 14" aria-hidden="true"><circle cx="7" cy="7" r="7" fill="#fff"/><g fill="none" stroke="var(--olive)" stroke-width=".8"><rect x="3.5" y="4.5" width="7" height="5"/><path d="M3.5,4.5 l3.5,3 3.5,-3"/></g></svg>
        info@larkmoorsite.com
      </li>
      <li>
        <svg class="contact-icon" viewBox="0 0 14 14" aria-hidden="true"><circle cx="7" cy="7" r="7" fill="#fff"/></svg>
        @larkmoorsite.com
      </li>
      <li>
        <svg class="contact-icon" viewBox="0 0 14 14" aria-hidden="true"><circle cx="7" cy="7" r="7" fill="#fff"/></svg>
        @larkmoorsite.com
      </li>
    </ul>
  </section>

</main>
</body>
</html>
```